Music Producer Website

I need a website designed for my music production company. We specialize in finding talented musicians and matching them with music producers all over the United States. A visitor can create a profile and/or upload their music demo and we submit it to thousands of music producers and production companies for review. In many cases, our members will receive multiple signing offers from music producers allowing them to choose the contract that is best for them. "We turn aspiring musicians into SuperStars!"
Please include photos that reflect all genres of music (black artists, white artists, both male and female.) We produce all types of music including rap, R&B, rock, country, and Hip Hop.
When a user creates a profile, they become visible to thousands of record producers who are looking to sign new talent and make them stars.
Somewhere in the top half of the page, please include a small form that the visitor can fill out. The form should look as follows:
Title (large and bold): Contact Us or Submit Music Demo
Fields to include (* = required): First Name*, Last Name*, Age, Zip Code, Email Address*, Daytime Phone, Evening Phone, Comments
Then, there will be a "submit" button to proceed to next step of form. Just below the "submit" button, should be the following verbiage: "After submitting, you will have the opportunity to upload demos of your music (optional) and provide other pertinent information about yourself, band, or group."
Updates
Reason: I have not seen a design that I am 100% satisfied with yet. Ideally, rotating header images (GIF or other) with several different music producers in studio (male, female, black, white) would be perfect. Here are some examples of how the header pics could look:
http://files.quillmarsh.net/art_img/514302/806421/806421_7391046_514302_image.jpg
http://files.quillmarsh.net/art_img/514302/806421/806421_7391058_514302_image.jpg
http://files.quillmarsh.net/art_img/514302/806421/806421_7391037_514302_image.jpg
Also, there should be a form on the site (somewhere in upper half of the page) with the following headline:
GET FOUND AND BECOME A STAR! (super large, super-bold font)
Contact Us or Submit Your Music for Review (large font, not as bold as headline)
First Name
Last Name
Age
Zip Code
Email Address
Daytime Phone
Evening Phone
Comments
Target Market(s)
We are targeting all types of musicians including rock, rap, pop, R&B, country, gospel, etc.
Industry/Entity Type
Artists
Colors
Designer to choose colors to be used in the design.
Look and feel
Each slider illustrates characteristics of the customer's brand and the style your logo design should communicate.

```html
<!DOCTYPE html>
<html lang="en">
<head>
<meta charset="utf-8">
<title>Velour Music Productions</title>
<link rel="stylesheet" href="https://fonts.googleapis.com/css2?family=Hind:wght@400;500;600&display=swap">
<style>
:root{
  --topbar:#1c1a19;
  --header:#0f0e0e;
  --nav:#231f1e;
  --gold:#8a6a1a;
  --page:#e4e1dc;
  --panel:#f2f2f2;
  --panel-line:#cfcfcf;
  --field:#e3e0dd;
  --ink:#2b2b2b;
  --link:#2a6fc9;
  --accent:#ff7a00;
}
*{box-sizing:border-box;margin:0;padding:0}
html,body{width:1200px;height:867px;overflow:hidden}
body{font-family:"Hind",sans-serif;background:var(--page);color:var(--ink);position:relative;font-size:12px}
.topbar{position:absolute;left:0;top:0;width:1200px;height:37px;background:var(--topbar);color:#ddd;font-size:13px}
.topbar .stat{position:absolute;top:10px;display:flex;align-items:center;gap:6px}
.upload-btn{position:absolute;left:966px;top:7px;background:#0c0b0b;color:#fff;padding:5px 9px 2px;border-radius:3px;font-size:13px}
.gold-line{position:absolute;left:0;top:37px;width:1200px;height:5px;background:var(--gold)}
.header{position:absolute;left:0;top:42px;width:1200px;height:115px;background:var(--header)}
.search-tab{position:absolute;left:600px;top:37px;width:229px;height:34px;background:var(--header);border-radius:0 0 16px 16px;color:#eee;font-size:17px;text-align:center;padding-top:8px;z-index:2}
.brand{position:absolute;left:141px;top:18px;display:flex;align-items:center;gap:10px;color:#d9b25a;font-size:22px;font-weight:600;letter-spacing:.5px}
.brand .dot{width:26px;height:26px;background:#d9b25a;border-radius:50%}
.search-box{position:absolute;left:622px;top:89px;width:436px;height:33px;background:#e6e6e6;border-radius:3px}
.search-box svg{position:absolute;right:13px;top:8px}
.search-hint{position:absolute;left:620px;top:128px;color:#888;font-size:11px;font-style:italic}
.adv{position:absolute;left:985px;top:128px;color:#999;font-size:11px;text-decoration:underline}
.nav{position:absolute;left:0;top:157px;width:1200px;height:40px;background:var(--nav)}
.nav a{position:absolute;top:9px;color:#ddd;font-size:15px;text-decoration:none;padding:3px 15px 0;height:25px}
.nav a.active{background:#0c0b0b;border-radius:3px;color:#fff}
.slider{position:absolute;left:141px;top:207px;width:639px;height:291px;background:radial-gradient(circle at 45% 35%,#3a4a52,#14252c 55%,#0b1418)}
.slider .arrow{position:absolute;top:115px;width:36px;height:36px;background:rgba(0,0,0,.55);display:flex;align-items:center;justify-content:center}
.caption{position:absolute;left:0;bottom:0;width:100%;height:65px;background:rgba(0,0,0,.55);padding:14px 20px}
.caption h2{color:var(--accent);font-weight:500;font-size:17px;line-height:1.2;white-space:nowrap}
.caption p{color:#eee;font-size:12px;margin-top:3px}
.panel{position:absolute;background:var(--panel);border:1px solid var(--panel-line);border-radius:4px}
.form-panel{left:788px;top:207px;width:270px;height:292px}
.form-panel h3{position:absolute;left:18px;top:12px;font-size:15px;font-weight:500;color:#333;white-space:nowrap;letter-spacing:-.1px}
.field{position:absolute;height:29px;background:var(--field);font-size:12px;color:#444;padding:8px 11px 0;white-space:nowrap}
.field.half-l{left:19px;width:113px}
.field.half-r{left:137px;width:116px}
.field.full{left:19px;width:234px}
.field i{color:#d00;font-style:normal}
.submit{position:absolute;left:19px;top:207px;background:var(--gold);color:#fff;font-size:14px;padding:6px 12px 3px}
.form-note{position:absolute;left:19px;top:243px;width:240px;font-size:9.5px;line-height:1.3;color:#333}
.recent{left:141px;top:510px;width:638px;height:268px}
.panel-head{margin:2px;height:36px;background:linear-gradient(#f7f7f7,#dcdcdc);border-radius:3px;font-size:17px;color:#333;display:flex;align-items:center;padding-left:10px;gap:14px}
.filters{font-size:12px;color:#333;padding:9px 18px 0;height:32px}
.tracks{display:grid;grid-template-columns:318px 318px;grid-auto-rows:38.5px}
.track{display:flex;align-items:center;position:relative;padding-left:20px}
.track:nth-child(4n+1),.track:nth-child(4n+2){background:#ebebeb}
.track:nth-child(4n+3),.track:nth-child(4n+4){background:#f6f6f6}
.track .num{width:22px;font-size:17px;color:#333}
.track .avatar{width:30px;height:30px;background:linear-gradient(#e8c9a8,#8e2a24);border-radius:3px;margin-right:12px}
.track .title{font-size:12px;line-height:1.3;color:#333;white-space:nowrap}
.track .title a{display:block;color:var(--link);text-decoration:none}
.play{position:absolute;right:8px;top:9px;width:61px;height:21px;border-radius:11px;background:linear-gradient(#fff,#d9d9d9);border:1px solid #ccc;font-size:11.5px;text-align:center;padding-top:3px}
.musician{left:788px;top:510px;width:270px;height:268px}
.musician .panel-head{justify-content:center;padding:0;font-size:17px}
.musician .name{text-align:center;font-weight:600;font-size:14px;margin-top:6px}
.portrait{margin:5px auto 0;width:209px;height:132px;border-radius:4px;background:linear-gradient(135deg,#6b5a4c,#2a211c 60%,#1a1411)}
.meta{padding:9px 0 0 33px;font-size:13.5px;line-height:1.7}
.meta .row{display:flex;align-items:center;white-space:nowrap}
.meta .row .label{margin-right:10px}
.stars{display:flex;gap:3px;align-items:center;margin-left:4px}
.footer{position:absolute;left:0;top:805px;width:1200px;height:62px;background:#000;color:#ddd;font-size:13px}
.footer .copy{position:absolute;left:141px;top:24px}
.social{position:absolute;left:902px;top:19px;display:flex;gap:13px}
.social span{width:30px;height:30px;border-radius:50%;background:#5a5a5a}
</style>
</head>
<body>
<div class="topbar">
  <div class="stat" style="left:141px"><svg width="15" height="15" viewBox="0 0 15 15"><circle cx="7.5" cy="4.5" r="3.5" fill="#9b7a2c"/><path d="M1 15c0-5 13-5 13 0z" fill="#9b7a2c"/></svg>1,72,000 K users online</div>
  <div class="stat" style="left:293px"><svg width="16" height="15" viewBox="0 0 24 23"><path d="M12 0l3.7 7.5 8.3 1.2-6 5.8 1.4 8.3L12 19l-7.4 3.8L6 14.5 0 8.7l8.3-1.2z" fill="#9b7a2c"/></svg>My Favourites</div>
  <div class="upload-btn">Upload Music</div>
</div>
<div class="gold-line"></div>
<div class="header">
  <div class="brand"><span class="dot"></span>Velour Music Productions</div>
</div>
<div class="search-tab">Search Music</div>
<div class="search-box"><svg width="17" height="17" viewBox="0 0 17 17"><circle cx="7" cy="7" r="5.5" fill="none" stroke="#111" stroke-width="2"/><path d="M11 11l5 5" stroke="#111" stroke-width="2.4"/></svg></div>
<div class="search-hint">Search music, albums, artists,</div>
<div class="adv">Advance Search</div>
<nav class="nav">
  <a class="active" style="left:141px">Main</a><a style="left:225px">Search</a><a style="left:301px">Control Panel</a><a style="left:418px">Post Music</a><a style="left:529px">News</a><a style="left:605px">Forum</a><a style="left:685px">FAQ</a><a style="left:754px">Contact</a>
</nav>

<div class="slider" role="img" aria-label="Photo of a female guitarist singing into a microphone on a lit stage">
  <div class="arrow" style="left:18px"><svg width="14" height="14" viewBox="0 0 14 14"><path d="M10 1L4 7l6 6" fill="none" stroke="#ccc" stroke-width="3"/></svg></div>
  <div class="arrow" style="right:15px"><svg width="14" height="14" viewBox="0 0 14 14"><path d="M4 1l6 6-6 6" fill="none" stroke="#ccc" stroke-width="3"/></svg></div>
  <div class="caption">
    <h2>Born to Win album challenged with its competers in the market</h2>
    <p>Composing with natural settings is a delite to the listeners says Nella Thorpe...</p>
  </div>
</div>

<form class="panel form-panel">
  <h3>Contact Us or Submit Music Demo</h3>
  <div class="field half-l" style="top:39px">First Name<i>*</i></div>
  <div class="field half-r" style="top:39px">Last Name<i>*</i></div>
  <div class="field half-l" style="top:72px">Age</div>
  <div class="field half-r" style="top:72px">Zipcode</div>
  <div class="field full" style="top:105px">Email Address<i>*</i></div>
  <div class="field half-l" style="top:139px">Daytime Phone</div>
  <div class="field half-r" style="top:139px">Evening Phone</div>
  <div class="field full" style="top:173px">Comments</div>
  <div class="submit">SUBMIT</div>
  <p class="form-note">After submitting, you will have the opportunity to upload demos of your music (optional) and provide other pertinent information about yourself, band, or group.</p>
</form>

<section class="panel recent">
  <div class="panel-head"><svg width="22" height="24" viewBox="0 0 22 24"><path d="M7 3l13-3v16" fill="none" stroke="#f39a1e" stroke-width="3"/><path d="M7 3v17" stroke="#f39a1e" stroke-width="3"/><circle cx="4.5" cy="20" r="4" fill="#f39a1e"/><circle cx="17.5" cy="17" r="4" fill="#f39a1e"/></svg>Recent Music's Uploaded</div>
  <div class="filters">All Time | This Month | This Week</div>
  <div class="tracks">
    <div class="track"><span class="num">1</span><span class="avatar" role="img" aria-label="Artist avatar"></span><div class="title">Just think easy<a>Anderson</a></div><span class="play">Play</span></div>
    <div class="track"><span class="num">2</span><span class="avatar" role="img" aria-label="Artist avatar"></span><div class="title">I am from Africa<a>Harris</a></div><span class="play">Play</span></div>
    <div class="track"><span class="num">3</span><span class="avatar" role="img" aria-label="Artist avatar"></span><div class="title">Thumbs up<a>Davis</a></div><span class="play">Play</span></div>
    <div class="track"><span class="num">4</span><span class="avatar" role="img" aria-label="Artist avatar"></span><div class="title">Welldone boy<a>Nelson</a></div><span class="play">Play</span></div>
    <div class="track"><span class="num">5</span><span class="avatar" role="img" aria-label="Artist avatar"></span><div class="title">Why dont dance?<a>Brown</a></div><span class="play">Play</span></div>
    <div class="track"><span class="num">6</span><span class="avatar" role="img" aria-label="Artist avatar"></span><div class="title">Struggle hard<a>Martin</a></div><span class="play">Play</span></div>
    <div class="track"><span class="num">7</span><span class="avatar" role="img" aria-label="Artist avatar"></span><div class="title">People are crazy<a>Matthew</a></div><span class="play">Play</span></div>
    <div class="track"><span class="num">8</span><span class="avatar" role="img" aria-label="Artist avatar"></span><div class="title">Sing when you can...<a>Young</a></div><span class="play">Play</span></div>
    <div class="track"><span class="num">9</span><span class="avatar" role="img" aria-label="Artist avatar"></span><div class="title">Jump Jump Jump High..<a>Moore</a></div><span class="play">Play</span></div>
    <div class="track" style="padding-left:8px"><span class="num" style="width:34px">10</span><span class="avatar" role="img" aria-label="Artist avatar"></span><div class="title">Popularize dreams<a>Robinson</a></div><span class="play">Play</span></div>
  </div>
</section>

<section class="panel musician">
  <div class="panel-head">Musician of the week</div>
  <div class="name">Martinez</div>
  <div class="portrait" role="img" aria-label="Portrait photo of the featured musician"></div>
  <div class="meta">
    <div class="row"><span class="label">Ratings:</span>
      <span class="stars">
        <svg width="17" height="17" viewBox="0 0 24 23"><path d="M12 0l3.7 7.5 8.3 1.2-6 5.8 1.4 8.3L12 19l-7.4 3.8L6 14.5 0 8.7l8.3-1.2z" fill="#f5c518" stroke="#c48a00"/></svg>
        <svg width="17" height="17" viewBox="0 0 24 23"><path d="M12 0l3.7 7.5 8.3 1.2-6 5.8 1.4 8.3L12 19l-7.4 3.8L6 14.5 0 8.7l8.3-1.2z" fill="#f5c518" stroke="#c48a00"/></svg>
        <svg width="17" height="17" viewBox="0 0 24 23"><path d="M12 0l3.7 7.5 8.3 1.2-6 5.8 1.4 8.3L12 19l-7.4 3.8L6 14.5 0 8.7l8.3-1.2z" fill="#f5c518" stroke="#c48a00"/></svg>
        <svg width="17" height="17" viewBox="0 0 24 23"><path d="M12 0l3.7 7.5 8.3 1.2-6 5.8 1.4 8.3L12 19l-7.4 3.8L6 14.5 0 8.7l8.3-1.2z" fill="#f5c518" stroke="#c48a00"/></svg>
        <svg width="17" height="17" viewBox="0 0 24 23"><path d="M12 0l3.7 7.5 8.3 1.2-6 5.8 1.4 8.3L12 19l-7.4 3.8L6 14.5 0 8.7l8.3-1.2z" fill="#f5c518" stroke="#c48a00"/></svg>
      </span>
    </div>
    <div class="row"><span class="label" style="margin-right:6px">Comments:</span><span>1345</span></div>
  </div>
</section>

<footer class="footer">
  <div class="copy">Copyright Velour Productions. All rights reserved.</div>
  <div class="social"><span></span><span></span><span></span><span></span></div>
</footer>
</body>
</html>
```